Oil and Gas Exploration and Production company needs a business card design

We need a business card design using our logo and colors in the logo. We want a mainstream design.

```html
<!DOCTYPE html>
<html lang="en">
<head>
<meta charset="utf-8">
<title>Tarsivo Energy – Business Card</title>
<link href="https://fonts.googleapis.com/css2?family=Arimo:wght@400;700&display=swap" rel="stylesheet">
<style>
  :root {
    --ink: #070707;
    --paper: #ffffff;
    --gold: #c99a32;
    --stage: #e6e3de;
  }
  * { margin: 0; padding: 0; box-sizing: border-box; }
  html, body {
    width: 1200px;
    height: 902px;
    overflow: hidden;
    background: var(--stage);
    font-family: "Arimo", Arial, sans-serif;
  }
  .card {
    position: absolute;
    left: 150px;
    top: 195px;
    width: 900px;
    height: 512px;
    border-radius: 26px;
    overflow: hidden;
    background: var(--ink);
    box-shadow: 0 10px 30px rgba(0,0,0,0.18);
  }
  .card-shapes { position: absolute; inset: 0; }
  .brand {
    position: absolute;
    left: 58px;
    top: 252px;
    transform: translateY(-50%);
    display: flex;
    align-items: center;
    gap: 12px;
  }
  .brand-dot {
    width: 38px;
    height: 38px;
    border-radius: 50%;
    background: var(--gold);
  }
  .brand-name {
    font-weight: 700;
    font-size: 40px;
    letter-spacing: -1px;
    color: var(--ink);
    line-height: 1;
    white-space: nowrap;
  }
  .person {
    position: absolute;
    left: 528px;
    top: 111px;
  }
  .person-name {
    font-weight: 700;
    font-size: 29px;
    color: var(--paper);
    line-height: 1;
  }
  .person-title {
    margin-top: 3px;
    font-size: 22px;
    color: var(--gold);
    line-height: 1;
  }
  .address {
    position: absolute;
    left: 528px;
    top: 247px;
    font-size: 21px;
    line-height: 28px;
    color: var(--paper);
  }
  .contacts {
    position: absolute;
    left: 528px;
    top: 309px;
    list-style: none;
  }
  .contact {
    display: flex;
    align-items: center;
    gap: 10px;
    height: 31px;
    font-size: 21px;
    color: var(--paper);
    white-space: nowrap;
  }
  .contact-icon { width: 25px; height: 25px; flex: none; }
</style>
</head>
<body>
  <div class="card">
    <svg class="card-shapes" width="900" height="512" viewBox="0 0 900 512">
      <path class="gold-swoosh" d="M450 60 C515 150 515 360 358 512 L300 512 L300 60 Z" fill="var(--gold)"/>
      <path class="white-panel" d="M-5 -5 H420 C480 80 490 300 305 517 H-5 Z"
            fill="var(--paper)" stroke="var(--paper)" stroke-width="3"/>
    </svg>

    <div class="brand">
      <span class="brand-dot"></span>
      <span class="brand-name">Tarsivo Energy</span>
    </div>

    <div class="person">
      <div class="person-name">Marcus Hale</div>
      <div class="person-title">President &amp; CEO</div>
    </div>

    <div class="address">PO Box 456, Harbour Road<br>3rd Lane, Redford</div>

    <ul class="contacts">
      <li class="contact">
        <svg class="contact-icon" viewBox="0 0 28 28">
          <circle cx="14" cy="14" r="12.5" fill="none" stroke="var(--gold)" stroke-width="2"/>
          <path d="M9 9 Q8 10 9 13 Q12 18 16 20 Q18 21 19 19 L17 16.5 L15.5 17.5 Q12.5 15.5 11 12.5 L12 11 Z" fill="var(--gold)"/>
        </svg>
        <span>(123) 555 0188</span>
      </li>
      <li class="contact">
        <svg class="contact-icon" viewBox="0 0 28 28">
          <circle cx="14" cy="14" r="12.5" fill="none" stroke="var(--gold)" stroke-width="2"/>
          <rect x="7.5" y="9.5" width="13" height="9" fill="var(--gold)"/>
          <path d="M7.5 9.5 L14 15 L20.5 9.5" fill="none" stroke="var(--ink)" stroke-width="1.2"/>
        </svg>
        <span>info@tarsivoenergy.com</span>
      </li>
      <li class="contact">
        <svg class="contact-icon" viewBox="0 0 28 28">
          <circle cx="14" cy="14" r="12.5" fill="none" stroke="var(--gold)" stroke-width="2"/>
          <circle cx="14" cy="14" r="7" fill="none" stroke="var(--gold)" stroke-width="1.4"/>
          <ellipse cx="14" cy="14" rx="3" ry="7" fill="none" stroke="var(--gold)" stroke-width="1.2"/>
          <path d="M7 14 H21 M8.5 10.5 H19.5 M8.5 17.5 H19.5" stroke="var(--gold)" stroke-width="1.1"/>
        </svg>
        <span>www.tarsivoenergy.com</span>
      </li>
    </ul>
  </div>
</body>
</html>
```